Stationery Set for Velmora Company

I need to create full stationery design for my company; Business Cards, Envelops, Letter Heads, Calendar.
In the letter head and Envelops... only contact information and website links.
Our company is a Service Management company with different domains of innovative services including Technology Service Management, Education Services, Outsourcing Management, Events Management.
I need a modern and innovative design specially for the business card. I some transparent designs and I like it, but don't limit your innovation to what I mentioned. Sky is limit for your innovation.

Target Market(s)

Middle East & Africa

Industry/Entity Type

Business Management

Colors
34a7d8
0355a3
85acd3
86cae7
cee9f5
cfdeed
e4daeb
f3f1f8
ecf7fb

Requirements
Must have
• Name, Title, Email, Mobile
Nice to have
• We have multiple locations in USA, KSA, EGY, so I need ideas about how to include all contact details maybe QR / Barcode or something else.
• Please see our locations and contact information: www.brightvelmora.example
Should not have
• Too much text

```html
<!DOCTYPE html>
<html lang="en">
<head>
<meta charset="utf-8">
<title>Velmora Company – Envelope</title>
<link rel="stylesheet" href="https://fonts.googleapis.com/css2?family=Quicksand:wght@500;700&display=swap">
<style>
  :root {
    --page: #ffffff;
    --silver-dark: #c9c7c8;
    --silver-mid: #dcdadb;
    --silver-light: #f1f0f1;
    --edge: #8e8e8e;
    --band: #ececec;
    --band-line: #9a9a9a;
    --brand-grey: #8c8c8c;
    --brand-blue: #34a7d8;
    --window: #ffffff;
    --sheen: rgba(255, 255, 255, 0.28);
  }
  * { margin: 0; padding: 0; box-sizing: border-box; }
  html, body {
    width: 1200px; height: 1000px; overflow: hidden;
    background: var(--page);
    font-family: "Quicksand", sans-serif;
  }
  .envelope {
    position: absolute; left: 38px; top: 80px;
    width: 1132px; height: 806px;
    border: 1px solid var(--edge);
    overflow: hidden;
    background:
      linear-gradient(90deg,
        var(--silver-mid) 0%, var(--silver-light) 6%, var(--silver-dark) 14%,
        var(--silver-mid) 24%, var(--silver-light) 33%, var(--silver-dark) 45%,
        var(--silver-mid) 55%, var(--silver-light) 66%, var(--silver-dark) 78%,
        var(--silver-light) 88%, var(--silver-mid) 100%);
  }
  .corner-sheen {
    position: absolute; left: 0; top: 60px;
    width: 510px; height: 290px;
    background: radial-gradient(ellipse at 20% 30%, var(--sheen) 0%, rgba(255,255,255,0) 70%);
  }
  .brand-name {
    position: absolute; left: 64px; top: 100px;
    font-size: 58px; font-weight: 700; letter-spacing: 1px;
    color: var(--brand-grey); line-height: 1;
  }
  .return-address {
    position: absolute; left: 67px; top: 243px;
    font-size: 20px; font-weight: 500; line-height: 31.5px;
    color: var(--brand-blue);
    font-style: normal;
  }
  .band {
    position: absolute; left: 0; right: 0; top: 665px; height: 41px;
    background: var(--band);
    border-top: 1px solid var(--band-line);
    border-bottom: 1px solid var(--band-line);
  }
  .address-window {
    position: absolute; left: 670px; top: 558px;
    width: 406px; height: 171px;
    background: var(--window);
    border: 1px solid var(--band-line);
    border-radius: 14px;
  }
</style>
</head>
<body>
  <div class="envelope">
    <div class="corner-sheen" role="img" aria-label="Faint decorative sweep behind the company name"></div>
    <div class="brand-name">Velmora</div>
    <address class="return-address">
      418 Harbor Crest Drive, 5th<br>
      Floor Lindale City CA 94021<br>
      US
    </address>
    <div class="band"></div>
    <div class="address-window"></div>
  </div>
</body>
</html>
```